Premium Business Card for Wealth Creation

Please see attached business card for example.
Happy to look at options like Blue background with Yellow
Target Market(s)
People who want to buy investment property or create wealth
Industry/Entity Type
Investment
Contact Information for Business Card
Tel: 1800 314 579
Mobile: 0417 265 904
Address: Level 1, 64 Carrow Lane Brighton Vic 3186
Name: Martin Feldway
Title: CEO
Website: www.quolvane.com.au
Email: martin@quolvane.com.au
Font styles to use
Sans Serif
Colors
0255a3
fbed22
Requirements
Must have
- Look great

```html
<!DOCTYPE html>
<html lang="en">
<head>
<meta charset="utf-8">
<title>Quolvane Business Card</title>
<link rel="stylesheet" href="https://fonts.googleapis.com/css2?family=Noto+Sans:wght@400;700&display=swap">
<style>
  :root {
    --brand-blue: #3953a4;
    --brand-yellow: #fcd22a;
    --yellow-light: #fbed22;
    --yellow-deep: #f8cd26;
    --card-white: #ffffff;
    --backdrop: #ecebe8;
  }
  * { margin: 0; padding: 0; box-sizing: border-box; }
  html, body {
    width: 1200px;
    height: 902px;
    overflow: hidden;
    background: var(--backdrop);
    font-family: "Noto Sans", Verdana, sans-serif;
  }
  .business-card {
    position: absolute;
    left: 100px;
    top: 166px;
    width: 1000px;
    height: 570px;
    background: var(--card-white);
    overflow: hidden;
    box-shadow: 0 2px 10px rgba(0,0,0,0.12);
  }
  .card-sweep {
    position: absolute;
    inset: 0;
    width: 100%;
    height: 100%;
  }
  .brand-mark {
    position: absolute;
    left: 58px;
    top: 61px;
    width: 106px;
    height: 106px;
    border-radius: 50%;
    background: var(--brand-yellow);
  }
  .brand-name {
    position: absolute;
    left: 180px;
    top: 75px;
    font-size: 75px;
    line-height: 1;
    font-weight: 700;
    color: var(--brand-blue);
    letter-spacing: 0.5px;
  }
  .person-name {
    position: absolute;
    left: 55px;
    top: 248px;
    font-size: 32px;
    line-height: 1;
    font-weight: 700;
    color: var(--brand-blue);
  }
  .person-title {
    position: absolute;
    left: 57px;
    top: 288px;
    font-size: 25px;
    line-height: 1;
    color: var(--brand-yellow);
  }
  .address {
    position: absolute;
    left: 55px;
    top: 329px;
    font-size: 26px;
    line-height: 32px;
    font-style: normal;
    color: var(--brand-blue);
  }
  .contact-list {
    position: absolute;
    left: 55px;
    top: 407px;
    list-style: none;
  }
  .contact-item {
    display: flex;
    align-items: center;
    height: 32px;
    font-size: 26px;
    line-height: 32px;
    color: var(--brand-blue);
  }
  .contact-icon {
    width: 27px;
    height: 27px;
    margin-right: 8px;
    flex: none;
    background: var(--brand-yellow);
    display: block;
  }
</style>
</head>
<body>
  <section class="business-card">
    <svg class="card-sweep" viewBox="0 0 940 536" preserveAspectRatio="none" aria-hidden="true">
      <defs>
        <linearGradient id="sweepYellow" x1="0" y1="0" x2="0" y2="1">
          <stop offset="0" stop-color="var(--yellow-light)"/>
          <stop offset="1" stop-color="var(--yellow-deep)"/>
        </linearGradient>
      </defs>
      <path class="sweep-yellow" fill="url(#sweepYellow)"
            d="M826,250 C822,380 785,470 728,536 L570,536 C700,495 800,400 826,250 Z"/>
      <path class="sweep-blue" fill="var(--brand-blue)"
            d="M757,0 C850,120 860,380 745,536 L940,536 L940,0 Z"/>
    </svg>

    <span class="brand-mark"></span>
    <div class="brand-name">QUOLVANE</div>

    <h1 class="person-name">Martin Feldway</h1>
    <p class="person-title">CEO</p>

    <address class="address">
      Level 3, 64 Carrow Lane<br>
      Larnwick Vic 3947
    </address>

    <ul class="contact-list">
      <li class="contact-item">
        <svg class="contact-icon" viewBox="0 0 27 27" aria-hidden="true">
          <path fill="#fff" d="M5 10c0-3 4-4 8.5-4S22 7 22 10v1h-4v-2h-9v2H5z"/>
          <path fill="#fff" d="M8 12h11l2 8H6z"/>
          <circle cx="13.5" cy="16" r="2" fill="var(--brand-yellow)"/>
        </svg>
        1800 314 579
      </li>
      <li class="contact-item">
        <svg class="contact-icon" viewBox="0 0 27 27" aria-hidden="true">
          <rect x="9" y="4" width="9" height="19" rx="1.5" fill="#fff"/>
          <rect x="10.5" y="6.5" width="6" height="7" fill="var(--brand-yellow)"/>
        </svg>
        0417 265 904
      </li>
      <li class="contact-item">
        <svg class="contact-icon" viewBox="0 0 27 27" aria-hidden="true">
          <rect x="4" y="7" width="19" height="13" fill="none" stroke="#fff" stroke-width="1.8"/>
          <path d="M4 7l9.5 7L23 7M4 20l7-6M23 20l-7-6" fill="none" stroke="#fff" stroke-width="1.6"/>
        </svg>
        martin@quolvane.com.au
      </li>
      <li class="contact-item">
        <svg class="contact-icon" viewBox="0 0 27 27" aria-hidden="true">
          <g fill="none" stroke="#fff" stroke-width="1.5">
            <circle cx="13.5" cy="13.5" r="8.5"/>
            <ellipse cx="13.5" cy="13.5" rx="3.8" ry="8.5"/>
            <path d="M5 13.5h17M6.5 9h14M6.5 18h14"/>
          </g>
        </svg>
        www.quolvane.com.au
      </li>
    </ul>
  </section>
</body>
</html>
```